Website Redesign Project

Brightwater Delivery Partners provides project management and project controls consultancy services to companies in many industry sectors, within Australia and overseas. My company has been developing a business brand through forging strong business relationships within industry. We provide innovative tools, concepts and solutions to management teams to assist them in better plan and managing there project portfolios.
SECTORS OF INDUSTRY WE SERVICE
★Oil & Gas
★Minerals & Metals
★Petrochemical
★Manufacturing
★Building & Construction
★Telecommunications
★Rail
★Civil
OLD WEBSITE
My old website www.brightwaterdeliverypartners-demo.com.au needs a complete overhaul in terms of how the web pages look and feel. I am trying to get away from the grey, washed out look as it is uninviting and dull. My clients commented that my webpage does not reflect who I am as a company or my core values. Think total redesign
DESIGN
I would like a webpage design that is modern and has a corporate image. It must be elegant, classy, and have an overall glossy appearance. I want something exciting that creates some excellent feedback from clients. It needs to have a savvy appearance and an attitude of a market leader. A generic website template cannot be used as I provide a unique service to clients. I do not need a website design that looks like my compeditors, I want something that stands out in the crowd and effectivly markets my bussinesses brand. I want my website to represent quality, so only high resolution images that are clear, sharp and in focus can be used. With this design, throw your standard webpage design concepts out the window, as I want something fresh, innovative, exciting and inviting. The overall design should appear uncluttered as all content needs to be there for a reason, so think functional.
It must be professional and of the highest calibre as my clients expect nothing less. I provide clients with innovative tools, concepts and solutions, so the design needs to be edgy and creative to align with my company’s core business services. The new design must promote the company’s brand and us as a market leader. It must communicate that we service many industry sectors and reflect our company’s creativity, vision, energy and drive.
WEBPAGE WRITTEN CONTENT
I am happy with the written content on each page within my old website. You may arrange the text how you see fit within the new design. On the main page of my old website the text is under scored, I am not a big fan of this. I currently do not like the format the text is in, I am looking for a formatt that is easy to read, looks flattering and pleasing to the eye.
MAIN PAGE DESIGN
The main page design needs to focus on my company as a brand, it must promote that I service many industry sectors. My old webpage had me pigeon holed as only providing services to oil and gas. This is incorrect as I service oil & gas, metals and minerals, Petrochemical, Manufacturing, Building & Construction, Telecommunications, Rail and civil.
WEBPAGE COLUR PREFERENCE
Prefer a white background with plenty of colour
TESTIMONIAL TAB
The testimonial tab on the task bar can be removed as it is no longer required.
FINISHED PRODUCT
The finished product will be uploaded by you to a nominated web hosting account. I will need a copy of all files associated with the design. A copy of the finished product will also be provided in formats that can me imported to Xara Pro Designer as I will update my website in 6 months or so using this tool.
Updates
I have updated the design brief after recieving feedback from several designers
Thanks
Reason: Some designers have asked for more time
Hi All
I have just launched another project called "brightwater delivery partners business card redesign project", you are all welcome to join this project.
Thanks
Target Market(s)
★Oil and Gas
★Mining and Resources
★Building and infrastructure
★Petrochemical
★Civil and roads
★Rail
Industry/Entity Type
Industry
Requirements
Must have
- ★Draw you in
★Hold your attention
★Identify company brand
★Highlight skills experience and expertise
★Be a unique design not generic
Should not have
- ★The webpage design should not be old fashioned
★ The design should not be based off a generic design template
★The webpage should not be cluttered; everything needs to be there for a reason.

```html
<!DOCTYPE html>
<html lang="en">
<head>
<meta charset="utf-8">
<title>Brightwater Delivery Partners – Contact</title>
<link rel="stylesheet" href="https://fonts.googleapis.com/css2?family=Source+Sans+3:wght@400;600;700&family=PT+Sans+Narrow:wght@400;700&display=swap">
<style>
:root{
  --red:#e0141c;
  --red-dark:#b3151d;
  --red-deep:#9c1118;
  --ink:#1c1c1c;
  --grey:#6f6f6f;
  --grey-light:#c9c9c9;
  --white:#ffffff;
  --footer-top:#2c2c2c;
  --footer-bottom:#141414;
  --hero-text:#f2e4c6;
}
*{box-sizing:border-box;margin:0;padding:0}
html,body{width:994px;height:1200px;overflow:hidden}
body{position:relative;background:var(--white);font-family:"Source Sans 3",Arial,sans-serif;color:var(--ink)}
.abs{position:absolute}

/* header */
.site-header{position:absolute;left:0;top:0;width:994px;height:92px;background:var(--white)}
.brand-mark{left:104px;top:14px;width:60px;height:60px;border-radius:50%;background:var(--red)}
.brand-name{left:176px;top:24px;font-size:23px;font-weight:700;color:var(--ink);white-space:nowrap;letter-spacing:-.2px}
.brand-tagline{left:177px;top:56px;font-size:8.5px;font-weight:600;color:var(--ink);white-space:nowrap}
.contact-icon{width:16px;height:16px}
.header-phone{left:669px;top:23px;font-size:18.5px;color:var(--red);white-space:nowrap}
.header-email{left:665px;top:53px;font-size:11px;color:var(--ink);white-space:nowrap}

/* navigation */
.main-nav{position:absolute;left:0;top:92px;width:994px;height:46px;background:linear-gradient(#e8161e,#d8121a 55%,#c8111a);border-bottom:1px solid #a80f15}
.nav-item{position:absolute;top:0;height:46px;line-height:46px;font-size:11.6px;color:var(--white);transform:translateX(-50%);white-space:nowrap}
.nav-item.active{top:7px;height:30px;line-height:30px;width:73px;text-align:center;border-radius:13px;background:linear-gradient(#2a2a2a,#050505)}
.nav-divider{position:absolute;top:0;width:1px;height:46px;background:#b50e15;box-shadow:1px 0 0 #ef3a40}

/* hero */
.hero{position:absolute;left:0;top:138px;width:994px;height:408px;background:linear-gradient(180deg,#8cc2e6 0%,#a8cce4 38%,#6e8fb2 62%,#35527e 80%,#1c3560 100%)}
.hero-arrow{position:absolute;width:34px;height:34px}
.hero-title{left:609px;top:110px;width:340px;font-family:"PT Sans Narrow",sans-serif;font-weight:700;font-size:18.5px;color:var(--hero-text);white-space:nowrap;padding-bottom:4px;border-bottom:1px solid #d9dfe6}
.hero-copy{left:611px;top:146px;width:340px;font-size:11px;line-height:17.4px;color:var(--hero-text)}

/* contact section */
.contact-band{position:absolute;left:0;top:546px;width:994px;height:506px;background:linear-gradient(var(--red-deep),var(--red-dark) 8%,var(--red-dark))}
.contact-card{position:absolute;left:98px;top:24px;width:813px;height:450px;background:var(--white);border-radius:6px;box-shadow:0 0 8px rgba(0,0,0,.25),inset 0 0 30px rgba(0,0,0,.06)}
.section-title{left:39px;top:45px;font-family:"PT Sans Narrow",sans-serif;font-weight:700;font-size:19.5px;color:#222}
.section-intro{left:41px;top:78px;font-size:14.2px;font-weight:400;color:#222;white-space:nowrap}
.form-heading{left:40px;top:141px;font-size:13.6px;font-weight:400;color:var(--grey);white-space:nowrap}
.field-label{position:absolute;left:40px;font-size:10.4px;color:#444}
.field-input{position:absolute;left:40px;width:203px;height:17px;border:1px solid #bdbdbd;background:var(--white)}
.field-area{height:39px}
.submit-btn{left:115px;top:369px;width:127px;height:20px;border-radius:3px;background:linear-gradient(#e01b22,#b9121a);color:var(--white);font-size:12px;text-align:center;line-height:20px}
.column-divider{left:347px;top:149px;width:1px;height:258px;background:#e3e3e3}
.map-area{left:377px;top:169px;width:189px;height:187px;background:linear-gradient(135deg,#ece7dc,#e2dccf);border:1px solid #cfcfcf}
.details-icon{left:580px;top:172px;width:22px;height:22px}
.details-heading{left:609px;top:173px;font-size:15px;line-height:20px;color:var(--grey);white-space:nowrap}
.details-name{left:578px;top:205px;font-size:15px;line-height:20px;color:var(--grey);white-space:nowrap}
.details-line{position:absolute;left:581px;font-size:10px;line-height:14px;color:#333;white-space:nowrap}

/* footer */
.site-footer{position:absolute;left:0;top:1052px;width:994px;height:148px;background:linear-gradient(var(--footer-top),var(--footer-bottom));border-top:1px dotted #6a2a2a}
.footer-title{left:126px;top:14px;font-family:"PT Sans Narrow",sans-serif;font-size:16px;color:var(--white)}
.footer-input{position:absolute;left:123px;width:227px;height:23px;background:var(--white);border:1px solid #8a8a8a;border-radius:2px;font-size:8.5px;font-style:italic;color:#999;padding:6px 10px}
.subscribe-btn{left:277px;top:125px;width:72px;height:21px;border:1px solid #e8e8e8;border-radius:4px;background:linear-gradient(#d61a21,#a3121a);color:var(--white);font-size:10.5px;font-weight:600;text-align:center;line-height:19px}
.social-tile{position:absolute;top:29px;width:21px;height:21px;border-radius:2px;background:#5d6670;box-shadow:0 1px 2px rgba(0,0,0,.5)}
.copyright{right:118px;top:78px;font-size:9.5px;color:#d8d8d8;text-align:right;white-space:nowrap;line-height:16px}
</style>
</head>
<body>

<header class="site-header">
  <div class="abs brand-mark"></div>
  <div class="abs brand-name">Brightwater Delivery Partners</div>
  <div class="abs brand-tagline">Providing Effective Project Controls and Management Solutions</div>

  <svg class="abs contact-icon" style="left:637px;top:26px" viewBox="0 0 16 16" aria-hidden="true">
    <rect width="16" height="16" rx="3" fill="#9a9a9a"/>
    <path d="M5 3.5c-.8.4-1.3 1.2-1 2.4.6 2.7 3.3 5.6 6 6.2 1.2.3 2-.2 2.4-1l-1.8-1.4-1.1.8c-1.3-.6-2.5-1.9-3-3.1l.8-1.1z" fill="#fff"/>
  </svg>
  <div class="abs header-phone">+ 61 0400 555 019</div>

  <svg class="abs contact-icon" style="left:637px;top:52px" viewBox="0 0 16 16" aria-hidden="true">
    <rect x=".5" y="2.5" width="15" height="11" fill="#fff" stroke="#777"/>
    <path d="M1 3l7 5.5L15 3M1 13l5-4.5M15 13l-5-4.5" fill="none" stroke="#777"/>
  </svg>
  <div class="abs header-email">d.marsh@brightwaterdp.com.au</div>
</header>

<nav class="main-nav">
  <span class="nav-item" style="left:142px">HOME</span>
  <span class="nav-divider" style="left:178px"></span>
  <span class="nav-item" style="left:222px">ABOUT US</span>
  <span class="nav-divider" style="left:264px"></span>
  <span class="nav-item" style="left:309px">EXPERTISE</span>
  <span class="nav-divider" style="left:350px"></span>
  <span class="nav-item" style="left:402px">KNOWLEDGE</span>
  <span class="nav-divider" style="left:452px"></span>
  <span class="nav-item" style="left:501px">EXPERIENCE</span>
  <span class="nav-divider" style="left:548px"></span>
  <span class="nav-item" style="left:591px">PROJECTS</span>
  <span class="nav-divider" style="left:635px"></span>
  <span class="nav-item" style="left:672px">FOCUS</span>
  <span class="nav-item active" style="left:751px">CONTACT</span>
  <span class="nav-item" style="left:843px">TESIMONIALS</span>
</nav>

<section class="hero" role="img" aria-label="Photograph of an offshore drilling rig lit up at dusk on a calm sea">
  <svg class="hero-arrow" style="left:43px;top:197px" viewBox="0 0 34 34" aria-hidden="true">
    <circle cx="17" cy="17" r="17" fill="#253345"/>
    <path d="M20 9l-8 8 8 8" fill="none" stroke="#fff" stroke-width="3.2" stroke-linecap="round"/>
  </svg>
  <svg class="hero-arrow" style="left:914px;top:197px" viewBox="0 0 34 34" aria-hidden="true">
    <circle cx="17" cy="17" r="17" fill="#253345"/>
    <path d="M14 9l8 8-8 8" fill="none" stroke="#fff" stroke-width="3.2" stroke-linecap="round"/>
  </svg>
  <h2 class="abs hero-title">PROJECT CONTROLS AND MANAGEMENT SOLUTIONS</h2>
  <p class="abs hero-copy">Cum sociis natoque penatibus et magnis dis parturient montes, nascetur ridiculus mus. In iaculis facilisis massa. Etiam eu urna. Sed porta.Cum sociis natoque penatibus et magnis dis parturient montes, nascetur ridiculus mus.</p>
</section>

<section class="contact-band">
  <div class="contact-card">
    <h1 class="abs section-title">Contact Us</h1>
    <p class="abs section-intro">To arrange a meeting or have a confidential discussion about how I can assist your business, please contact me on</p>

    <h3 class="abs form-heading">Kindly post your valuable Suggestions &amp;&nbsp; Query</h3>
    <label class="field-label" style="top:175px">Enter your Name</label>
    <div class="field-input" style="top:192px"></div>
    <label class="field-label" style="top:216px">Enter your Email</label>
    <div class="field-input" style="top:233px"></div>
    <label class="field-label" style="top:255px">Enter your Phone Number</label>
    <div class="field-input" style="top:275px"></div>
    <label class="field-label" style="top:295px">Add Your Comments Here:</label>
    <div class="field-input field-area" style="top:309px"></div>
    <div class="abs submit-btn">Submit Query</div>

    <div class="abs column-divider"></div>

    <div class="abs map-area" role="img" aria-label="Street map showing the office location with a red pin"></div>

    <svg class="abs details-icon" viewBox="0 0 22 22" aria-hidden="true">
      <rect width="22" height="22" rx="4" fill="#dcdcdc"/>
      <path d="M7.5 5c-1.1.5-1.8 1.6-1.4 3.3.8 3.6 4.4 7.4 8 8.1 1.6.4 2.6-.3 3.1-1.3l-2.4-1.8-1.4 1c-1.7-.8-3.3-2.5-4-4.1l1-1.5z" fill="#fff"/>
    </svg>
    <div class="abs details-heading">Contact Details</div>
    <div class="abs details-name">Daniel Marsh</div>
    <div class="details-line" style="top:237px">#12 Harbour Road, Lorem ipsum,</div>
    <div class="details-line" style="top:257px">Phone:&nbsp; 0400555019</div>
    <div class="details-line" style="top:277px">E-mail:</div>
    <div class="details-line" style="top:297px">d.marsh@ brightwaterdp .com.au</div>
    <div class="details-line" style="top:317px">Website :</div>
    <div class="details-line" style="top:337px;left:584px">www.brightwaterdeliverypartners-demo.com.au</div>
  </div>
</section>

<footer class="site-footer">
  <h4 class="abs footer-title">NEWSLETTER</h4>
  <div class="footer-input" style="top:50px">Name</div>
  <div class="footer-input" style="top:86px">your email address here..</div>
  <div class="abs subscribe-btn">Subscribe &rsaquo;</div>

  <span class="social-tile" style="left:695px"></span>
  <span class="social-tile" style="left:727px"></span>
  <span class="social-tile" style="left:759px"></span>
  <span class="social-tile" style="left:791px"></span>
  <span class="social-tile" style="left:823px"></span>
  <span class="social-tile" style="left:855px"></span>

  <div class="abs copyright">© 2013 brightwaterdeliverypartners-demo.com.au, All rights reserved<br>x2</div>
</footer>

</body>
</html>
```